Redesign of business card for Cedar Ridge Mechanical

We are looking for a new design for our business cards for Cedar Ridge Mechanical. We are a plumbing & HVAC construction company, operating on the West Coast of Canada and USA. Logo attached.
Industry/Entity Type
Construction - Plumbing & HVAC
Contact Information for Business Card
Name, address, phone numbers, email, website address
Look and feel
Each slider illustrates characteristics of the customer's brand and the style your logo design should communicate.

```html
<!DOCTYPE html>
<html lang="en">
<head>
<meta charset="utf-8">
<title>Cedar Ridge Mechanical – Business Card</title>
<link rel="stylesheet" href="https://fonts.googleapis.com/css2?family=Oswald:wght@500&family=Montserrat:wght@400;500;700&display=swap">
<style>
  :root {
    --backdrop: #e6e3de;
    --card-white: #ffffff;
    --ink: #1c1c1c;
    --ink-soft: #2a2a2a;
    --card-black: #0b0b0b;
    --card-grey: #3a3a3a;
    --on-dark: #ffffff;
  }
  * { margin: 0; padding: 0; box-sizing: border-box; }
  html, body { width: 900px; height: 1200px; overflow: hidden; }
  body {
    background: var(--backdrop);
    font-family: "Montserrat", Arial, sans-serif;
    color: var(--ink);
    position: relative;
  }
  .card {
    position: absolute;
    left: 80px;
    width: 742px;
    height: 441px;
    border-radius: 24px;
    overflow: hidden;
    box-shadow: 0 6px 18px rgba(0,0,0,0.18);
  }
  .card-front { top: 131px; background: var(--card-white); }
  .card-back  { top: 638px; background: var(--card-black); }

  .company-title {
    position: absolute;
    left: 25px; top: 54px;
    font-family: "Oswald", "Arial Narrow", sans-serif;
    font-weight: 500;
    font-size: 37px;
    letter-spacing: 2px;
    line-height: 1;
    color: var(--ink);
  }
  .person {
    position: absolute;
    right: 35px; top: 50px;
    text-align: right;
  }
  .person-name { font-weight: 700; font-size: 25px; line-height: 1.1; }
  .person-role { font-weight: 500; font-size: 16px; margin-top: 3px; }

  .address {
    position: absolute;
    left: 36px; top: 235px;
    font-size: 16px; line-height: 20px;
  }
  .contacts {
    position: absolute;
    left: 36px; top: 316px;
    list-style: none;
    font-size: 16px;
  }
  .contacts li {
    display: flex; align-items: center; gap: 11px;
    height: 30px;
  }
  .contacts svg { width: 16px; height: 16px; fill: var(--ink-soft); flex: none; }

  .brand-mark {
    position: absolute;
    right: 36px; bottom: 40px;
    display: flex; align-items: center; gap: 12px;
    font-weight: 700; font-size: 24px; color: var(--ink);
  }
  .brand-mark .block { width: 26px; height: 26px; background: var(--ink); }

  .back-field {
    position: absolute; inset: 0;
    background: radial-gradient(ellipse at 8% 10%, var(--card-grey) 0%, #1a1a1a 38%, var(--card-black) 70%);
  }
  .back-brand {
    position: absolute;
    right: 28px; top: 312px;
    display: flex; align-items: center; gap: 8px;
    font-weight: 700; font-size: 13px; color: var(--on-dark);
  }
  .back-brand .block { width: 14px; height: 14px; background: var(--on-dark); }
</style>
</head>
<body>
  <section class="card card-front" aria-label="Business card front">
    <h1 class="company-title">CEDAR RIDGE MECHANICAL</h1>
    <div class="person">
      <p class="person-name">Daniel Hart</p>
      <p class="person-role">Managing Director</p>
    </div>
    <address class="address" style="font-style:normal">
      214 Birchwood Lane<br>Ridgeland, MS 39157
    </address>
    <ul class="contacts">
      <li>
        <svg viewBox="0 0 24 24" aria-hidden="true"><path d="M6.6 10.8a15.1 15.1 0 0 0 6.6 6.6l2.2-2.2a1 1 0 0 1 1-.25 11.4 11.4 0 0 0 3.6.57 1 1 0 0 1 1 1V20a1 1 0 0 1-1 1A17 17 0 0 1 3 4a1 1 0 0 1 1-1h3.5a1 1 0 0 1 1 1c0 1.25.2 2.45.57 3.6a1 1 0 0 1-.25 1z"/></svg>
        888.555.0142
      </li>
      <li>
        <svg viewBox="0 0 24 24" aria-hidden="true"><path d="M2 5h20v14H2z M2 5l10 7 10-7" /></svg>
        info@cedarridgemechanical.com
      </li>
      <li>
        <svg viewBox="0 0 24 24" aria-hidden="true"><circle cx="12" cy="12" r="10"/></svg>
        www.cedarridgemechanical.com
      </li>
    </ul>
    <div class="brand-mark">
      <span class="block"></span>
      <span>Cedar Ridge Mechanical</span>
    </div>
  </section>

  <section class="card card-back" aria-label="Business card back">
    <div class="back-field" role="img" aria-label="Glossy repeating brand pattern on black"></div>
    <div class="back-brand">
      <span class="block"></span>
      <span>Cedar Ridge Mechanical</span>
    </div>
  </section>
</body>
</html>
```